Heron Loan Partners Business Card

We need a business card design for our mortgage servicing company. In addition to servicing the loans of homeowners, we help homeowners with purchasing their homes and any mortgage refinancing. We would like to see designs that use the colors in the logo attached below (gold-ish yellow and navy blue), and any other design you deem fit! The design should communicate a simpler life with smart mortgages provided by Heron.

```html
<!DOCTYPE html>
<html lang="en">
<head>
<meta charset="utf-8">
<title>Heron Loan Partners Business Card</title>
<link rel="stylesheet" href="https://fonts.googleapis.com/css2?family=Poppins:wght@400;600&family=Raleway:wght@500&display=swap">
<style>
  :root {
    --navy: #261f52;
    --gold: #e0b13c;
    --white: #ffffff;
    --backdrop: #ababab;
  }
  * { box-sizing: border-box; margin: 0; padding: 0; }
  html, body {
    width: 1093px;
    height: 1200px;
    overflow: hidden;
    background: var(--backdrop);
    font-family: "Poppins", sans-serif;
  }
  .card {
    position: absolute;
    left: 265px;
    width: 580px;
    height: 356px;
    border-radius: 27px;
    overflow: hidden;
  }
  .card-front { top: 226px; background: var(--white); }
  .card-front .base-band {
    position: absolute;
    left: 0; right: 0; bottom: 0;
    height: 12px;
    background: var(--navy);
  }
  .card-back { top: 621px; background: var(--navy); }

  .wordmark {
    position: absolute;
    left: 0; right: 0;
    top: 90px;
    text-align: center;
    font-family: "Poppins", sans-serif;
    font-weight: 600;
    font-size: 38px;
    letter-spacing: 0.5px;
    color: var(--gold);
  }
  .card-back .wordmark { top: 152px; }

  .holder {
    position: absolute;
    right: 317px;
    top: 218px;
    text-align: right;
  }
  .holder-name {
    font-family: "Raleway", sans-serif;
    font-weight: 500;
    font-size: 23px;
    line-height: 28px;
    color: var(--gold);
  }
  .holder-role {
    font-size: 16px;
    line-height: 20px;
    color: var(--navy);
  }
  .divider {
    position: absolute;
    left: 288px;
    top: 220px;
    width: 2px;
    height: 57px;
    background: var(--gold);
  }
  .contacts {
    position: absolute;
    left: 307px;
    top: 215px;
    list-style: none;
  }
  .contacts li {
    display: flex;
    align-items: center;
    height: 21px;
    font-size: 17px;
    color: var(--navy);
  }
  .contacts svg {
    width: 15px;
    height: 15px;
    margin-right: 8px;
    flex: none;
  }
  .contacts .accent { color: var(--gold); }
  .address {
    position: absolute;
    left: 0; right: 0;
    top: 306px;
    text-align: center;
    font-size: 16px;
    color: var(--navy);
  }
</style>
</head>
<body>
  <section class="card card-front">
    <div class="wordmark">Heron Loan Partners</div>

    <div class="holder">
      <p class="holder-name">Daniel Reyes</p>
      <p class="holder-role">Managing Director</p>
    </div>
    <div class="divider"></div>

    <ul class="contacts">
      <li>
        <svg viewBox="0 0 16 16" aria-hidden="true"><path d="M3.5 1.5l2.5 3-1.6 1.6c.8 1.8 2.2 3.2 4 4l1.6-1.6 3 2.5-1.6 2.4C6.6 13.2 2.8 9.4 1.2 3.1z" fill="none" stroke="#e0b13c" stroke-width="1.4" stroke-linejoin="round"/><path d="M10 2a4 4 0 014 4M10 4.5a1.6 1.6 0 011.5 1.5" fill="none" stroke="#e0b13c" stroke-width="1.3" stroke-linecap="round"/></svg>
        044-555 010 234
      </li>
      <li>
        <svg viewBox="0 0 16 16" aria-hidden="true"><rect x="1" y="3" width="14" height="10" fill="#e0b13c"/><path d="M1 3l7 6 7-6M1 13l5-4.5M15 13l-5-4.5" fill="none" stroke="#ffffff" stroke-width="1.2"/></svg>
        hello@heronloans.com
      </li>
      <li>
        <svg viewBox="0 0 16 16" aria-hidden="true"><g fill="none" stroke="#e0b13c" stroke-width="1.3"><circle cx="8" cy="8" r="6.5"/><ellipse cx="8" cy="8" rx="2.8" ry="6.5"/><path d="M1.5 8h13M2.5 4.8h11M2.5 11.2h11"/></g></svg>
        <span>www.<span class="accent">heronloans</span>.com</span>
      </li>
    </ul>

    <p class="address">77 Wharf Street, Bay City 40213, Country Name</p>
    <div class="base-band"></div>
  </section>

  <section class="card card-back">
    <div class="wordmark">Heron Loan Partners</div>
  </section>
</body>
</html>
```